Irrigation Business needs their business cards modernised and revamped

I would like to keep my current logo, colours and revamp the format of the card.

I would like the card to be clean yet important.

Im not sure if you include texture but i would like the named logo to be indented into the card etc.

show me something alive and free something thats clinical to the point yet has a feel of achievement. i would like people to go nice card.

Target Market(s)

high end clients, corporate, sports field manger, the guys that make the decisions

Industry/Entity Type

Business

Contact Information for Business Card

nformation to be included

Dean Harlow (Director)
0487305526
dean@kolvat.biz
www.kestonfieldworks.com

instagram logo
google logo
facebook logo

Colors

Designer to choose colors to be used in the design.

Requirements
Nice to have
• indentations a really nice feel to the card good texture

```html
<!DOCTYPE html>
<html lang="en">
<head>
<meta charset="utf-8">
<title>Keston Fieldworks – Business Card</title>
<link rel="stylesheet" href="https://fonts.googleapis.com/css2?family=Mulish:wght@400;600;700;800&display=swap">
<style>
  :root {
    --stage: #2e2f31;
    --card-white: #ffffff;
    --card-black-top: #1f2022;
    --card-black-bottom: #0e0e10;
    --brand-blue: #2f6db8;
    --brand-sky: #2aa3d9;
    --brand-deep: #2a5aa8;
    --text-grey: #6b6f75;
    --accent-teal: #3fb6b0;
  }
  * { box-sizing: border-box; margin: 0; padding: 0; }
  html, body {
    width: 1200px; height: 674px; overflow: hidden;
    background: var(--stage);
    font-family: "Mulish", Arial, sans-serif;
  }
  .canvas { position: relative; width: 1200px; height: 674px; }

  .card {
    position: absolute; top: 244px; width: 330px; height: 188px;
    border-radius: 10px; overflow: hidden;
    box-shadow: 0 6px 18px rgba(0,0,0,0.45);
  }
  .card--front { left: 267px; background: var(--card-white); }
  .card--back {
    left: 602px;
    background: linear-gradient(160deg, var(--card-black-top), var(--card-black-bottom));
  }

  .decor-panel {
    position: absolute; top: 5px; width: 90px; height: 178px;
    background: linear-gradient(160deg, var(--brand-sky), var(--brand-deep));
    opacity: 0.9;
  }
  .card--front .decor-panel { left: 240px; }
  .card--back .decor-panel { left: 0; }

  .brand { position: absolute; display: flex; flex-direction: column; align-items: center; }
  .brand__dot {
    width: 35px; height: 35px; border-radius: 50%;
    background: var(--brand-sky); margin-bottom: 7px;
  }
  .brand__name {
    font-weight: 800; font-size: 9.5px; letter-spacing: -0.2px; line-height: 1;
    color: var(--brand-blue); white-space: nowrap; text-transform: uppercase;
  }
  .card--front .brand { left: 14px; top: 17px; width: 110px; }
  .card--back .brand { left: 196px; top: 107px; width: 120px; }
  .card--back .brand__dot { width: 38px; height: 38px; margin-bottom: 7px; }
  .card--back .brand__name { font-size: 10.5px; }

  .holder { position: absolute; left: 21px; top: 106px; }
  .holder__name { font-size: 11px; font-weight: 700; color: var(--brand-blue); line-height: 1.2; }
  .holder__role { font-size: 7.5px; color: var(--text-grey); margin-top: 1px; }
  .holder__rule { width: 10px; height: 1.5px; background: var(--accent-teal); margin-top: 6px; }

  .contacts { position: absolute; left: 22px; top: 142px; list-style: none; }
  .contacts li {
    display: flex; align-items: center; gap: 7px;
    font-size: 7.5px; color: var(--text-grey); height: 10.5px;
  }
  .contacts li.contacts__web { color: var(--brand-blue); }
  .contacts svg { width: 6px; height: 6px; fill: var(--brand-blue); }

  .social { position: absolute; left: 172px; top: 165px; display: flex; gap: 4px; }
  .social span { width: 8px; height: 8px; border-radius: 2px; background: var(--text-grey); }
</style>
</head>
<body>
<main class="canvas">
  <section class="card card--front">
    <div class="decor-panel" role="img" aria-label="Large brand emblem decoration, left half"></div>
    <div class="brand">
      <span class="brand__dot"></span>
      <span class="brand__name">Keston Fieldworks</span>
    </div>
    <div class="holder">
      <p class="holder__name">Dean Harlow</p>
      <p class="holder__role">Director</p>
      <div class="holder__rule"></div>
    </div>
    <ul class="contacts">
      <li><svg viewBox="0 0 10 10"><path d="M2 0h2l1 3-1.5 1a6 6 0 0 0 2.5 2.5L7 5l3 1v2c0 1-1 2-2 2A8 8 0 0 1 0 2c0-1 1-2 2-2z"/></svg>0487305526</li>
      <li><svg viewBox="0 0 10 10"><path d="M0 2h10v6H0z"/></svg>dean@kolvat.biz</li>
      <li class="contacts__web"><svg viewBox="0 0 10 10"><circle cx="5" cy="5" r="5"/></svg>www.kestonfieldworks.com</li>
    </ul>
    <div class="social" aria-hidden="true"><span></span><span></span><span></span></div>
  </section>

  <section class="card card--back">
    <div class="decor-panel" role="img" aria-label="Large brand emblem decoration, right half"></div>
    <div class="brand">
      <span class="brand__dot"></span>
      <span class="brand__name">Keston Fieldworks</span>
    </div>
  </section>
</main>
</body>
</html>
```